Exclusive beauty salon needs a price list or services booklet

I need a new very attractive flyer for my beauty salon, containing information on the different services and their prices.
In attachment you can find a pdf of the "old" one, but I'd love to have a beautifully designed new one!
I'd love to have a booklet in format 148 x 148 mm, or in US format, containing 12 or 16 pages, but if you can offer other nice looking designs they are welcome!
The services that need to come in the booklet with their prices can all be found on my website: www.atelierverano.be, starting with
Gelaatsverzorging
Wimperverlenging
Suikerontharing
Wimperlifting
Permanente Make Up
Airbrush Tanning

Target Market(s)

woman from 20 to 89 years old

Industry/Entity Type

Beauty Salon

Font styles to use
Sans Serif

Colors

Designer to choose colors to be used in the design.

Requirements
Must have
• a classy nice look, it must contain details about the services from my beauty salon and their prices, and nice pictures.
• The Names, prices and explanations of the services can easily be found on my website: www.atelierverano.be
Nice to have
• In attachment you can find the "old" price list in pdf, what I need now is a "new booklet" with the new logo and updated services price list.
• I need a very nice and attractive looking booklet, classy chique, Paris chique, looking very expensive.
Should not have
• Not too much colors, not too curly, but still feminine

```html
<!DOCTYPE html>
<html lang="nl">
<head>
<meta charset="utf-8">
<title>Permanente Make Up – Prijslijst</title>
<link href="https://fonts.googleapis.com/css2?family=Open+Sans:ital,wght@0,400;0,600;1,700&family=Noto+Serif:wght@400&display=swap" rel="stylesheet">
<style>
:root{
  --plum:#a65b7e;
  --white:#ffffff;
  --ink:#1c1c1c;
  --teal:#7ec6bc;
  --teal-light:#acdad1;
  --teal-pale:#c7e6e0;
  --sky:#abd8e9;
  --sky-light:#b9dfee;
  --skin-light:#f4e4dc;
  --skin-mid:#e3c1b2;
}
*{margin:0;padding:0;box-sizing:border-box}
html,body{width:1200px;height:600px;overflow:hidden;background:var(--white)}
.sheet{position:relative;width:1200px;height:600px;display:flex;font-family:"Open Sans",sans-serif;color:var(--ink)}
.intro{width:436px;height:600px;display:flex;flex-direction:column}
.intro-panel{height:318px;overflow:hidden;background:var(--plum);color:var(--white);padding:26px 18px 0 18px;font-family:"Noto Serif",serif}
.intro-title{font-family:"Open Sans",sans-serif;font-weight:400;font-size:19px;letter-spacing:.3px;text-align:center;margin-bottom:16px}
.intro-panel p{font-size:11.6px;line-height:17.6px;text-align:justify;margin-bottom:17px}
.intro-photo{flex:1;background:linear-gradient(120deg,var(--skin-light),var(--skin-mid) 70%,var(--skin-light))}
.services{flex:1;display:flex;flex-direction:column}
.service{display:flex;height:85.7px;border-bottom:1px solid var(--white)}
.service-photo{width:162px;flex:none;background:linear-gradient(135deg,#d9cfc9,#8d7f78)}
.service-photo.brow{background:linear-gradient(180deg,#ffffff,#e9e9e9)}
.service-photo.lips{background:linear-gradient(135deg,#e8c8bd,#b5636b)}
.service-photo.violet{background:linear-gradient(135deg,#d9c7e6,#6a4c9c)}
.service-body{flex:1;padding:4px 6px 0 6px;font-size:10px;line-height:13.2px;overflow:hidden}
.service-name{font-weight:600;font-size:13.4px;letter-spacing:.1px;margin-bottom:2px}
.lead{font-weight:700;font-style:italic}
.service-price{width:67px;flex:none;display:flex;align-items:center;justify-content:center;font-size:23px}
.row-1 .service-body{background:var(--white)} .row-1 .service-price{background:var(--teal)}
.row-2 .service-body{background:var(--sky)} .row-2 .service-price{background:var(--sky-light)}
.row-3 .service-body{background:var(--teal-light)} .row-3 .service-price{background:var(--teal-pale)}
.row-4 .service-body{background:var(--teal)} .row-4 .service-price{background:var(--sky-light)}
.row-5 .service-body{background:var(--white)} .row-5 .service-price{background:var(--teal-pale)}
.row-6 .service-body{background:var(--sky)} .row-6 .service-price{background:var(--sky)}
.row-7 .service-body{background:var(--teal-light)} .row-7 .service-price{background:var(--white)}
</style>
</head>
<body>
<main class="sheet">
  <section class="intro">
    <div class="intro-panel">
      <h1 class="intro-title">PERMANENTE MAKE UP</h1>
      <p>Permanente make-up zit altijd goed en zorgt ervoor dat je er altijd verzorgd uitziet. Eyeliners, lipliners of wenkbrauw-accenten worden permanent aangebracht. Zo zie je er tijdens het sporten, als je uit bed stapt, als je op vakantie uit zee komt, als je een fikse strandwandeling maakt of in de regen hebt gefietst, toch verzorgd uit. Permanente make-up blijft altijd op z’n plaats, daardoor oogt je gezicht ook na het verwijderen van je make-up niet ‘kaal’. De aangebrachte accenten zorgen voor een sprekend gezicht en dat scheelt dagelijks een hoop tijd!</p>
      <p>Over permanente make-up moet je niet in een opwelling beslissen, je krijgt alle kans om er na het eerste consult nog eens goed over na te denken en ook als je er van af ziet, is dat geen enkel probleem. We zetten het alleen als je er 100% zeker van bent.</p>
    </div>
    <div class="intro-photo" role="img" aria-label="Foto van rode lippen en een hand met verzorgde nagels"></div>
  </section>

  <section class="services">
    <article class="service row-1">
      <div class="service-photo lips" role="img" aria-label="Close-up van lippen met permanente lipcontour"></div>
      <div class="service-body">
        <h2 class="service-name">FULL LIPS</h2>
        Een kleuraccent aan uw mond<br>•Uw hertekende liplijn preciseert uw natuurlijke mond • Een schaduweffect waarbij de liplijn uitschaduwt op de mond • Full lips vervolledigt de natuurlijke lipkleur • Camoufleert oneffenheden zoals pigmentvlekjes, hypopigmentatie • Vergroot boven en/ of onderlip • Full lips kleurt de mond volledig
      </div>
      <div class="service-price">€595</div>
    </article>
    <article class="service row-2">
      <div class="service-photo" role="img" aria-label="Close-up van een oog met volledige oogcontour"></div>
      <div class="service-body">
        <h2 class="service-name">PERMANENTE MAKE UP VOLLEDIGE OOGCONTOUR</h2>
        <span class="lead">Je tekent al jarenlang een lijntje boven en onder uw oog?</span> Een perfecte vorm is nodig want dit vervangt wel degelijk uw make-up! Ik ben altijd eerlijk en oprecht want uw mooie liner is mijn beste reclame! Ik geef heel graag advies over de mogelijkheden. Alles wordt uitvoerig besproken en uitgetekend zo ziet u al hoe uw eyeliner er zal uitzien en kan u zelf aangeven of u deze fijner of net iets dikker wenst.
      </div>
      <div class="service-price">€360</div>
    </article>
    <article class="service row-3">
      <div class="service-photo" role="img" aria-label="Close-up van een oog met brede eyeliner"></div>
      <div class="service-body">
        <h2 class="service-name">BREDE EYELINER BOVEN HET OOG</h2>
        <span class="lead">Je tekent al jarenlang een “dikker” lijntje ?</span> Een perfecte vorm is nodig want dit vervangt wel degelijk uw make-up! Ik ben altijd eerlijk en oprecht want uw mooie liner is mijn beste reclame! Ik geef heel graag advies over de mogelijkheden. Alles wordt uitvoerig besproken en uitgetekend zo ziet u al hoe uw eyeliner er zal uitzien en kan u zelf aangeven of u deze fijner of net iets dikker wenst.
      </div>
      <div class="service-price">€235</div>
    </article>
    <article class="service row-4">
      <div class="service-photo violet" role="img" aria-label="Close-up van een oog met fijne eyeliner"></div>
      <div class="service-body">
        <h2 class="service-name">FIJNE EYELINER BOVEN (WIMPERINVULLING) HET OOG</h2>
        De fijne eyeliner of wimperinvulling om uw ogen op een subtiele manier iets meer accentueren en laten spreken! Een eye-liner met subtiele klasse! • Uw ogen zullen meer spreken en u hoeft zich geen zorgen meer te maken over uitgelopen lijntjes of panda ogen. • Een echte Liner zonder het too much effect.
      </div>
      <div class="service-price">€186</div>
    </article>
    <article class="service row-5">
      <div class="service-photo brow" role="img" aria-label="Tekening van een wenkbrauw met hairstrokes"></div>
      <div class="service-body">
        <h2 class="service-name">WENKBRAUWEN HAIRSTROKE TECHNIEK</h2>
        <span class="lead">Voor wie?</span> ● Je wenst een hyper realistisch natuurlijk resultaat ● Je hebt weinig tot geen eigen haartjes ● Je bent het niet gewend om make up op je wenkbrauwen te gebruiken<br><span class="lead">Oplossing:</span> ● Er worden hairstrokes (fijne haartjes) gepigmenteerd op de huid ● Voor een vollere wenkbrauw ● Met een heel natuurlijke look
      </div>
      <div class="service-price">€320</div>
    </article>
    <article class="service row-6">
      <div class="service-photo brow" role="img" aria-label="Tekening van een gevulde poederwenkbrauw"></div>
      <div class="service-body">
        <h2 class="service-name">WENKBRAUWEN SHADING BROW OF POEDERWENKBRAUW</h2>
        <span class="lead">Voor wie?</span> ● Je wil elke dag mooi gevormde wenkbrauwen ● Je houdt van de soft make up look ● Je hebt weinig tot voldoende eigen haartjes<br><span class="lead">Oplossing:</span> ● Intensere kleur geven aan de wenkbrauw ● Mooie vorm geven aan de wenkbrauw ● Voor een mooie, zachte make up look
      </div>
      <div class="service-price">€320</div>
    </article>
    <article class="service row-7">
      <div class="service-photo brow" role="img" aria-label="Tekening van een uitgesproken wenkbrauw"></div>
      <div class="service-body">
        <h2 class="service-name">WENKBRAUWEN POWER BROW</h2>
        <span class="lead">Voor wie?</span> ● Je wenst een meer uitgesproken resultaat ● Je draagt dagelijks make up aan de wenkbrauwen ● Je hebt voldoende haartjes<br><span class="lead">Oplossing:</span> ● Shading techniek + Hairstroke techniek = Power brow ● Voller maken van de eigen wenkbrauw ● Meer kleur en vorm geven Voor de echte make up look Gezien bij Lena Moreau
      </div>
      <div class="service-price">€320</div>
    </article>
  </section>
</main>
</body>
</html>
```